Brimlow Plumbing Solutions

This is for my new plumbing company, I have attached an example of what I’m going for but want it to look better.

Target Market(s)

Home owners, real estate, etc.

Industry/Entity Type

Plumbing

Font styles to use
Other font styles liked:
• As per my logo and other examples uploaded

Colors

Designer to choose colors to be used in the design.

Requirements
Must have
• Must include my logo provided and similar to my flyer I have attached but better

```html
<!DOCTYPE html>
<html lang="en">
<head>
<meta charset="utf-8">
<title>Brimlow Plumbing Solutions – Flyer</title>
<link href="https://fonts.googleapis.com/css2?family=Montserrat:wght@400;500;600;800&display=swap" rel="stylesheet">
<style>
  :root{
    --ink:#333333;
    --blue:#6597e8;
    --blue-deep:#2f5fc4;
    --blue-light:#a9c6f5;
    --white:#ffffff;
  }
  html,body{margin:0;padding:0;overflow:hidden;background:var(--white);}
  .flyer{position:relative;width:860px;height:1200px;overflow:hidden;background:var(--white);font-family:"Montserrat",Arial,sans-serif;color:var(--ink);}
  .backdrop{position:absolute;inset:0;}
  .brand{position:absolute;left:64px;top:150px;color:var(--blue);font-weight:800;line-height:1;}
  .brand-name{font-size:54px;letter-spacing:1px;}
  .brand-sub{font-size:17px;letter-spacing:1.2px;margin-top:8px;padding-left:4px;}
  .brand-rule{position:absolute;left:68px;top:307px;width:225px;height:3px;background:var(--blue);}
  .tagline{position:absolute;left:71px;top:334px;margin:0;color:var(--white);font-size:15px;line-height:18px;font-weight:500;}
  .offer{position:absolute;left:589px;top:444px;width:200px;text-align:center;color:var(--white);}
  .offer-lead{font-size:19px;line-height:24px;font-weight:400;}
  .offer-amount{color:var(--blue);font-weight:800;font-size:24px;line-height:28px;margin-top:4px;}
  .offer-word{color:var(--blue);font-weight:800;font-size:24px;line-height:28px;}
  .services-title{position:absolute;left:74px;top:636px;margin:0;color:var(--white);font-size:29px;font-weight:500;letter-spacing:.5px;}
  .service{position:absolute;width:250px;margin-left:-125px;text-align:center;}
  .service-icon{display:block;margin:0 auto;width:64px;height:64px;}
  .service-label{margin:9px 0 0;font-size:17px;line-height:21px;font-weight:500;color:var(--ink);text-transform:uppercase;}
  .contact{position:absolute;top:1118px;text-align:center;color:var(--white);}
  .contact svg{display:block;margin:0 auto 6px;}
  .contact-text{font-size:13px;font-weight:500;}
  .contact-social{font-size:17px;}
  .social-dots{display:flex;justify-content:center;gap:10px;margin-bottom:6px;}
  .social-dots span{width:16px;height:16px;border-radius:50%;background:var(--blue);}
</style>
</head>
<body>
<div class="flyer">
  <svg class="backdrop" width="860" height="1200" viewBox="0 0 860 1200">
    <defs>
      <linearGradient id="photoTone" x1="0" y1="0" x2="1" y2="1">
        <stop offset="0" stop-color="#5d8fe8"/>
        <stop offset=".5" stop-color="#2f54a8"/>
        <stop offset="1" stop-color="#1c2a4a"/>
      </linearGradient>
    </defs>
    <rect x="0" y="395" width="860" height="421" fill="var(--blue)"/>
    <path d="M300,13 L850,13 L850,290 L570,540 Q520,585 470,540 L300,370 Z" fill="url(#photoTone)" role="img" aria-label="Photo of a plumber in gloves fitting white pipes"/>
    <path d="M300,395 L470,560 Q520,606 570,560 L850,306" fill="none" stroke="var(--white)" stroke-width="16"/>
    <path d="M0,13 L300,13 L430,160 Q468,200 430,240 L150,520 Q117,553 84,520 L0,436 Z" fill="var(--ink)"/>
    <path d="M365,13 L470,130 Q520,200 470,270 L160,580 Q117,620 70,580 L0,515" fill="none" stroke="var(--ink)" stroke-width="4"/>
    <rect x="-98" y="-98" width="196" height="196" rx="34" transform="translate(689,526) rotate(45)" fill="var(--white)"/>
    <rect x="-88" y="-88" width="176" height="176" rx="30" transform="translate(689,526) rotate(45)" fill="var(--ink)"/>
    <path d="M0,628 H357 A27,27 0 0 1 357,681 H0 Z" fill="var(--ink)"/>
    <line x1="290" y1="709" x2="290" y2="1099" stroke="var(--ink)" stroke-width="3"/>
    <line x1="559" y1="709" x2="559" y2="1099" stroke="var(--ink)" stroke-width="3"/>
    <rect x="0" y="1099" width="860" height="101" fill="var(--ink)"/>
  </svg>

  <div class="brand">
    <div class="brand-name">BRIMLOW</div>
    <div class="brand-sub">PLUMBING SOLUTIONS</div>
  </div>
  <div class="brand-rule"></div>
  <p class="tagline">Your local reliable Sydney plumber<br>Specialising in all aspects of<br>Plumbing, Drainage &amp;<br>Gas Maintenance.</p>

  <div class="offer">
    <div class="offer-lead">Mention<br>this flyer<br>to receive</div>
    <div class="offer-amount">15%</div>
    <div class="offer-word">DISCOUNT</div>
  </div>

  <h2 class="services-title">OUR SERVICES :</h2>

  <div class="service" style="left:174px;top:698px">
    <svg class="service-icon" viewBox="0 0 64 64"><circle cx="32" cy="32" r="31" fill="var(--ink)"/><path d="M20,22 l5,-3 4,7 -3,3 q3,6 9,9 l3,-3 7,4 -3,5 q-14,1 -22,-22z" fill="none" stroke="var(--white)" stroke-width="2"/><text x="40" y="27" fill="var(--white)" font-size="13" font-weight="600" font-family="Montserrat,sans-serif" text-anchor="middle">24</text></svg>
    <p class="service-label">Emergency<br>Plumbing</p>
  </div>
  <div class="service" style="left:425px;top:698px">
    <svg class="service-icon" viewBox="0 0 64 64"><circle cx="32" cy="32" r="31" fill="var(--ink)"/><path d="M20,20 v14 q0,10 12,10 q12,0 12,-10 v-14 M26,20 v14 q0,5 6,5 q6,0 6,-5 v-14 M17,20 h12 M35,20 h12 M30,44 v6 h4 v-6" fill="none" stroke="var(--white)" stroke-width="2"/></svg>
    <p class="service-label">Plumbing<br>Maintenance</p>
  </div>
  <div class="service" style="left:690px;top:698px">
    <svg class="service-icon" viewBox="0 0 64 64"><circle cx="32" cy="32" r="31" fill="var(--ink)"/><path d="M22,20 h14 v12 h-8 v-6 h-6z M28,32 v4" fill="none" stroke="var(--white)" stroke-width="2"/><circle cx="27" cy="42" r="2" fill="var(--white)"/><circle cx="32" cy="46" r="2" fill="var(--white)"/><circle cx="24" cy="48" r="2" fill="var(--white)"/><path d="M38,40 l8,8" stroke="var(--white)" stroke-width="2.5"/></svg>
    <p class="service-label">Drainage<br>Maintenance</p>
  </div>

  <div class="service" style="left:174px;top:829px">
    <svg class="service-icon" viewBox="0 0 64 64"><circle cx="32" cy="32" r="31" fill="var(--ink)"/><circle cx="32" cy="32" r="15" fill="none" stroke="var(--white)" stroke-width="2" stroke-dasharray="6 3"/><path d="M32,23 q8,8 5,14 q-5,6 -10,0 q-2,-5 3,-8 q0,4 3,5 q0,-6 -1,-11z" fill="none" stroke="var(--white)" stroke-width="2"/></svg>
    <p class="service-label">Gas<br>Maintenance</p>
  </div>
  <div class="service" style="left:425px;top:829px">
    <svg class="service-icon" viewBox="0 0 64 64"><circle cx="32" cy="32" r="31" fill="var(--ink)"/><rect x="25" y="17" width="14" height="26" rx="5" fill="none" stroke="var(--white)" stroke-width="2"/><path d="M32,27 q4,4 0,8 q-4,-4 0,-8z M19,28 h6 M39,28 h6 M20,47 h24" fill="none" stroke="var(--white)" stroke-width="2"/></svg>
    <p class="service-label">Hot Water<br>Systems</p>
  </div>
  <div class="service" style="left:690px;top:829px">
    <svg class="service-icon" viewBox="0 0 64 64"><circle cx="32" cy="32" r="31" fill="var(--ink)"/><path d="M16,28 h14 v-6 h6 v12 h-20z M33,34 v5" fill="none" stroke="var(--white)" stroke-width="2"/><path d="M33,43 q3,4 0,6 q-3,-2 0,-6z" fill="var(--white)"/><path d="M42,18 l7,12 h-14z M42,22 v4" fill="none" stroke="var(--white)" stroke-width="2"/></svg>
    <p class="service-label">Leaking<br>Fixtures</p>
  </div>

  <div class="service" style="left:174px;top:960px">
    <svg class="service-icon" viewBox="0 0 64 64"><circle cx="32" cy="32" r="31" fill="var(--ink)"/><path d="M20,20 h18 q6,0 6,6 v6 h-8 v-4 h-16z M38,32 q0,10 -6,14 M44,32 q0,12 -6,16 M16,48 h32" fill="none" stroke="var(--white)" stroke-width="2"/></svg>
    <p class="service-label">Blocked Sewer<br>&amp; Stormwater</p>
  </div>
  <div class="service" style="left:425px;top:960px">
    <svg class="service-icon" viewBox="0 0 64 64"><circle cx="32" cy="32" r="31" fill="var(--ink)"/><path d="M32,46 q-12,-12 -12,-20 a12,12 0 0 1 24,0 q0,8 -12,20z" fill="none" stroke="var(--white)" stroke-width="2"/><rect x="26" y="22" width="12" height="9" rx="2" fill="none" stroke="var(--white)" stroke-width="2"/><circle cx="32" cy="26.5" r="2.5" fill="none" stroke="var(--white)" stroke-width="1.5"/><ellipse cx="32" cy="48" rx="14" ry="4" fill="none" stroke="var(--white)" stroke-width="2"/></svg>
    <p class="service-label">Camera<br>&amp; Locating</p>
  </div>
  <div class="service" style="left:690px;top:960px">
    <svg class="service-icon" viewBox="0 0 64 64"><circle cx="32" cy="32" r="31" fill="var(--ink)"/><rect x="17" y="17" width="30" height="30" rx="3" fill="none" stroke="var(--white)" stroke-width="2"/><path d="M17,24 h30 M22,30 h20" stroke="var(--white)" stroke-width="2"/><circle cx="32" cy="39" r="5" fill="none" stroke="var(--white)" stroke-width="2"/></svg>
    <p class="service-label">TMV<br>Maintenance</p>
  </div>

  <div class="contact" style="left:32px;width:160px">
    <svg width="20" height="20" viewBox="0 0 20 20"><path d="M3,2 l4,-1 2,5 -2,2 q2,4 5,5 l2,-2 5,2 -1,4 q-10,1 -15,-15z" fill="var(--blue)"/></svg>
    <div class="contact-text">0400 615 293</div>
  </div>
  <div class="contact" style="left:218px;width:320px">
    <svg width="22" height="18" viewBox="0 0 22 18"><rect x="1" y="1" width="20" height="16" fill="var(--blue)"/><path d="M1,1 l10,9 10,-9" fill="none" stroke="var(--ink)" stroke-width="2"/></svg>
    <div class="contact-text">HELLO@BRIMLOWPLUMBING.COM.AU</div>
  </div>
  <div class="contact" style="left:560px;width:260px">
    <div class="social-dots"><span></span></div>
    <div class="contact-social">@BrimlowPlumbing</div>
  </div>
</div>
</body>
</html>
```